Design a New Business Card for Our Company

We are looking for fresh, unique, and a modern business card that reflects our roots as digital marketing agency focused on SEM.

Industry/Entity Type

Marketing

Contact Information for Business Card

looking for very unique out of the box designs. clean and modern that compliments our logo

Requirements
Must have
• colors should match our logo
• Front should have name, address, email, and phone/fax of the person, phone/fax are the same number
• back should have our url

```html
<!DOCTYPE html>
<html lang="en">
<head>
<meta charset="utf-8">
<title>Corvane Solutions – Business Card</title>
<link rel="stylesheet" href="https://fonts.googleapis.com/css2?family=Open+Sans:wght@400;600;700&display=swap">
<style>
  :root {
    --brand-blue: #5b97cf;
    --brand-grey: #a8a8a8;
    --text-grey: #555a60;
    --card-white: #ffffff;
    --backdrop: #e9eaec;
  }
  * { margin: 0; padding: 0; box-sizing: border-box; }
  html, body { width: 1200px; height: 900px; overflow: hidden; }
  body {
    background: var(--backdrop);
    font-family: "Open Sans", Arial, sans-serif;
    position: relative;
  }
  .card {
    position: absolute;
    width: 580px;
    height: 332px;
    box-shadow: 0 4px 14px rgba(0,0,0,0.12);
    overflow: hidden;
  }
  .brand { white-space: nowrap; }
  .brand-dot { flex: none; border-radius: 50%; }

  /* Back side */
  .card-back {
    left: 560px; top: 80px;
    background: var(--brand-blue);
    color: var(--card-white);
    text-align: center;
  }
  .card-back .brand {
    position: absolute; left: 0; right: 0; top: 110px;
    display: flex; justify-content: center; align-items: center; gap: 16px;
  }
  .card-back .brand-dot { width: 46px; height: 46px; background: var(--card-white); }
  .card-back .brand-name { font-size: 40px; font-weight: 700; letter-spacing: 0.5px; }
  .card-back .website { position: absolute; left: 0; right: 0; top: 230px; font-size: 17px; }

  /* Front side */
  .card-front {
    left: 60px; top: 480px;
    background: var(--card-white);
    color: var(--text-grey);
  }
  .card-front .decor { position: absolute; inset: 0; }
  .person { position: absolute; left: 66px; top: 22px; }
  .person-name { color: var(--brand-blue); font-weight: 700; font-size: 18px; line-height: 1.2; }
  .person-title { font-size: 13px; line-height: 1.3; }
  .contact { position: absolute; left: 30px; top: 140px; font-size: 14px; line-height: 20px; }
  .contact .address { margin-bottom: 6px; }
  .contact-line { display: flex; align-items: center; gap: 8px; }
  .contact-line svg { width: 12px; height: 12px; fill: var(--brand-blue); flex: none; }
  .card-front .brand {
    position: absolute; left: 232px; top: 140px;
    display: flex; align-items: center; gap: 12px;
  }
  .card-front .brand-dot { width: 38px; height: 38px; background: var(--brand-blue); }
  .card-front .brand-name { font-size: 28px; font-weight: 700; color: var(--brand-grey); }
</style>
</head>
<body>

<section class="card card-back" aria-label="Card back">
  <div class="brand">
    <span class="brand-dot"></span>
    <span class="brand-name">Corvane Solutions</span>
  </div>
  <p class="website">www.corvane.com</p>
</section>

<section class="card card-front" aria-label="Card front">
  <svg class="decor" viewBox="0 0 580 332" width="580" height="332" aria-hidden="true">
    <polygon points="0,0 56,0 30,40 0,40" fill="var(--brand-grey)"/>
    <polygon points="0,0 22,0 0,22" fill="var(--brand-blue)"/>
    <polygon points="0,252 300,252 292,270 0,270" fill="var(--brand-blue)"/>
    <polygon points="306,262 580,262 580,332 276,332" fill="var(--brand-grey)"/>
  </svg>

  <div class="person">
    <p class="person-name">Daniel Morrow</p>
    <p class="person-title">Managing Director</p>
  </div>

  <div class="contact">
    <p class="address">12345, Address Goes Here<br>Country Name, 123456.</p>
    <p class="contact-line">
      <svg viewBox="0 0 24 24"><path d="M6.6 10.8a15.1 15.1 0 0 0 6.6 6.6l2.2-2.2a1 1 0 0 1 1-.25 11.4 11.4 0 0 0 3.6.57 1 1 0 0 1 1 1V20a1 1 0 0 1-1 1A17 17 0 0 1 3 4a1 1 0 0 1 1-1h3.5a1 1 0 0 1 1 1c0 1.25.2 2.45.57 3.57a1 1 0 0 1-.25 1z"/></svg>
      055-246 813 570
    </p>
    <p class="contact-line">
      <svg viewBox="0 0 24 24"><path d="M6 2h10v6H6zM3 9h18v10h-3v3H6v-3H3zM8 15v5h8v-5z"/></svg>
      055-246 813 570
    </p>
    <p class="contact-line">
      <svg viewBox="0 0 24 24"><path d="M2 5h20v14H2zm2 2v.5l8 5 8-5V7l-8 5z"/></svg>
      info@corvane.com
    </p>
  </div>

  <div class="brand">
    <span class="brand-dot"></span>
    <span class="brand-name">Corvane Solutions</span>
  </div>
</section>

</body>
</html>
```